Banner for a National Dental Conference

We need a banner logo for our next Dental Conference in 2017. Our theme is 'Challenging the Status Quo'.
It must have the words '20 years of oral health therapy in Victoria' and the conference date and venue:
7-8th April 2017
Marlowe The Dunes Lodge, Torquay, Victoria.
It must also feature our association logo as attached.
Please be creative, however, we would like a 'clean' design, not cluttered.
The design is intended for use in the conference program and website.

Target Market(s)

Dental practitioners

Industry/Entity Type

Dental

Requirements
Must have
• As above.

```html
<!DOCTYPE html>
<html lang="en">
<head>
<meta charset="utf-8">
<title>Oral Health Conference Banner</title>
<link href="https://fonts.googleapis.com/css2?family=Roboto+Condensed:wght@400;500;700&family=Michroma&family=Montserrat:wght@500&display=swap" rel="stylesheet">
<style>
  :root {
    --page-bg: #ece9e4;
    --card-bg: #ffffff;
    --brand-purple: #5b2d8e;
    --band-purple: #55308c;
    --band-green: #146a4a;
    --date-green: #0f6b48;
    --ink: #1f1f1f;
    --swirl: #e8eef4;
    --photo-light: #eadbd0;
    --photo-mid: #c89d86;
    --photo-dark: #3b2a24;
  }
  html, body {
    margin: 0;
    width: 1200px;
    height: 711px;
    overflow: hidden;
    background: var(--page-bg);
  }
  .banner {
    position: absolute;
    left: 0;
    top: 107px;
    width: 1106px;
    height: 458px;
    transform: scale(1.085);
    transform-origin: top left;
    background: var(--card-bg);
    overflow: hidden;
    font-family: "Roboto Condensed", "Arial Narrow", sans-serif;
  }
  .banner__swirl {
    position: absolute;
    inset: 0;
    background:
      radial-gradient(ellipse 520px 90px at 260px 250px, var(--swirl), transparent 70%),
      radial-gradient(ellipse 600px 60px at 300px 330px, #f1f4f8, transparent 70%);
  }
  .banner__photo {
    position: absolute;
    right: 0;
    top: 0;
    width: 530px;
    height: 100%;
    background:
      radial-gradient(ellipse 190px 230px at 330px 210px, var(--photo-light), var(--photo-mid) 70%, transparent 100%),
      linear-gradient(90deg, transparent 0%, var(--photo-dark) 22%, #5a4036 55%, var(--photo-dark) 100%);
    -webkit-mask-image: linear-gradient(90deg, transparent 0, #000 18%);
    mask-image: linear-gradient(90deg, transparent 0, #000 18%);
  }
  .brand {
    position: absolute;
    left: 56px;
    top: 56px;
    display: flex;
    align-items: center;
    gap: 18px;
  }
  .brand__dot {
    width: 22px;
    height: 22px;
    border-radius: 50%;
    background: var(--brand-purple);
  }
  .brand__name {
    font-family: "Montserrat", sans-serif;
    font-weight: 500;
    font-size: 78px;
    letter-spacing: 3px;
    line-height: 1;
    color: var(--brand-purple);
  }
  .band {
    position: absolute;
    left: 0;
    display: flex;
    align-items: center;
    color: #fff;
  }
  .band--theme {
    top: 177px;
    width: 640px;
    height: 60px;
    padding-left: 54px;
    box-sizing: border-box;
    background: linear-gradient(90deg, var(--band-purple) 75%, rgba(85,48,140,0));
    font-weight: 700;
    font-size: 30px;
    letter-spacing: 0.3px;
  }
  .band--anniversary {
    top: 391px;
    width: 620px;
    height: 32px;
    padding-left: 54px;
    box-sizing: border-box;
    background: linear-gradient(90deg, var(--band-green) 75%, rgba(20,106,74,0));
    font-weight: 400;
    font-size: 19px;
    letter-spacing: 0.4px;
  }
  .event-date {
    position: absolute;
    left: 48px;
    top: 262px;
    margin: 0;
    line-height: 1;
    white-space: nowrap;
  }
  .event-date__days {
    font-weight: 700;
    font-size: 50px;
    color: var(--date-green);
  }
  .event-date__year {
    font-family: "Michroma", sans-serif;
    font-size: 42px;
    color: var(--ink);
    margin-left: 6px;
  }
  .venue {
    position: absolute;
    left: 50px;
    top: 325px;
    margin: 0;
    font-weight: 500;
    font-size: 22px;
    color: var(--ink);
  }
</style>
</head>
<body>
  <section class="banner">
    <div class="banner__swirl"></div>
    <div class="banner__photo" role="img" aria-label="Portrait photograph of a smiling woman with curly dark hair"></div>

    <div class="brand">
      <span class="brand__dot"></span>
      <span class="brand__name">ORALIS</span>
    </div>

    <div class="band band--theme">CHALLENGING THE STATUS QUO</div>

    <p class="event-date">
      <span class="event-date__days">7-8th APRIL</span>
      <span class="event-date__year">2017</span>
    </p>
    <p class="venue">Marlowe The Dunes Lodge, Torquay, Victoria.</p>

    <div class="band band--anniversary">20 YEARS OF ORAL HEALTH THERAPY IN VICTORIA</div>
  </section>
</body>
</html>
```